Working Capital graphics

Our business advisory firm requires 9 images to be re-created and improved in the branding of our business.

The 9 images have been uploaded below and the colours and branding of the business can be found at the website www.tallowmereadvisory.com.au

```html
<!DOCTYPE html>
<html lang="en">
<head>
<meta charset="utf-8">
<title>Next $100 of Sales Volume – Working Capital Cycle</title>
<link rel="stylesheet" href="https://fonts.googleapis.com/css2?family=Arimo:wght@400&family=Libre+Baskerville:wght@700&display=swap">
<style>
  :root {
    --bg: #ffffff;
    --ink: #141414;
    --ink-on-dark: #ffffff;
    --revenue: #7f1420;
    --cost-of-sales: #f26f2a;
    --operating: #b9213a;
    --distributions: #fbbd1a;
    --working-capital: #ef3f62;
    --funding: #f69322;
    --shortfall: #ec1f3a;
    --hub: #a89a90;
    --flag: #ee2a3e;
    --flag-soft: #ef4b66;
    --pole: #9a9a9a;
  }
  html, body {
    margin: 0;
    padding: 0;
    width: 1200px;
    height: 1000px;
    overflow: hidden;
    background: var(--bg);
  }
  .cycle-diagram {
    display: block;
    width: 1200px;
    height: 1000px;
  }
  .segment-label,
  .milestone-label {
    font-family: "Arimo", Arial, sans-serif;
    font-size: 21px;
    text-anchor: middle;
  }
  .segment-label { fill: var(--ink-on-dark); }
  .segment-label--dark { fill: var(--ink); }
  .milestone-label { fill: var(--ink); }
  .hub-title {
    font-family: "Libre Baskerville", Georgia, serif;
    font-weight: 700;
    font-size: 42px;
    fill: var(--ink-on-dark);
    text-anchor: middle;
  }
  .seg-revenue { fill: var(--revenue); }
  .seg-cost-of-sales { fill: var(--cost-of-sales); }
  .seg-operating { fill: var(--operating); }
  .seg-distributions { fill: var(--distributions); }
  .seg-working-capital { fill: var(--working-capital); }
  .seg-funding { fill: var(--funding); }
  .seg-shortfall { fill: var(--shortfall); }
  .hub-gap { fill: var(--bg); }
  .hub { fill: var(--hub); }
  .flag-pole { stroke: var(--pole); stroke-width: 3.5; stroke-linecap: round; }
  .flag-cloth { fill: var(--flag); }
  .flag--soft .flag-cloth { fill: var(--flag-soft); }
</style>
</head>
<body>
<svg class="cycle-diagram" viewBox="0 0 1200 1000" xmlns="http://www.w3.org/2000/svg" aria-labelledby="diagram-title">
  <title id="diagram-title">Next $100 of sales volume: from revenue through costs, distributions, working capital and funding</title>
  <defs>
    <symbol id="milestone-flag" viewBox="0 0 48 62">
      <line class="flag-pole" x1="6" y1="6" x2="18" y2="58"/>
      <path class="flag-cloth" d="M6 8 C15 2 22 12 32 7 L44 4 L41 22 C31 27 22 18 10 24 Z"/>
    </symbol>
  </defs>

  <g class="ring">
    <path class="seg-revenue" d="M625 474 L525 300.8 L509.6 173.4 L426.5 130.2 A397 397 0 0 1 611.1 77.2 L664.2 154.4 L618 274.1 Z"/>
    <path class="seg-cost-of-sales" d="M625 474 L618 274.1 L664.2 154.4 L611.1 77.2 A397 397 0 0 1 954.1 252 L916.8 337.9 L790.8 362.2 Z"/>
    <path class="seg-operating" d="M625 474 L790.8 362.2 L916.8 337.9 L954.1 252 A397 397 0 0 1 968.8 672.5 L875.2 676.6 L798.2 574 Z"/>
    <path class="seg-distributions" d="M625 474 L798.2 574 L875.2 676.6 L968.8 672.5 A397 397 0 0 1 659.6 869.5 L602.5 795.2 L642.4 673.2 Z"/>
    <path class="seg-working-capital" d="M625 474 L642.4 673.2 L602.5 795.2 L659.6 869.5 A397 397 0 0 1 288.3 684.4 L328.6 599.8 L455.4 580 Z"/>
    <path class="seg-funding" d="M625 474 L455.4 580 L328.6 599.8 L288.3 684.4 A397 397 0 0 1 284.7 269.5 L378.3 267 L453.6 371 Z"/>
    <path class="seg-shortfall" d="M625 474 L453.6 371 L378.3 267 L284.7 269.5 A397 397 0 0 1 426.5 130.2 L509.6 173.4 L525 300.8 Z"/>
  </g>

  <circle class="hub-gap" cx="625" cy="474" r="238"/>
  <circle class="hub" cx="625" cy="474" r="220"/>
  <text class="hub-title" x="622" y="466">Next $100 of</text>
  <text class="hub-title" x="622" y="516">Sales Volume</text>

  <g class="segment-labels">
    <text class="segment-label" x="576" y="163">$0</text>
    <text class="segment-label" x="780" y="211">Cost of Sales</text>
    <text class="segment-label" x="940" y="421">Operating</text>
    <text class="segment-label" x="940" y="448">Expenses</text>
    <text class="segment-label" x="934" y="565">Fixed</text>
    <text class="segment-label" x="934" y="592">Costs</text>
    <text class="segment-label segment-label--dark" x="846" y="710">Tax</text>
    <text class="segment-label segment-label--dark" x="782" y="764">Interest</text>
    <text class="segment-label segment-label--dark" x="693" y="810">Dividends</text>
    <text class="segment-label" x="550" y="789">Inv</text>
    <text class="segment-label" x="550" y="816">Days</text>
    <text class="segment-label" x="447" y="746">AP</text>
    <text class="segment-label" x="447" y="773">Days</text>
    <text class="segment-label" x="375" y="674">AR</text>
    <text class="segment-label" x="375" y="701">Days</text>
    <text class="segment-label" x="303" y="455">Additional</text>
    <text class="segment-label" x="303" y="482">Debt</text>
    <text class="segment-label" x="431" y="213">Cash</text>
    <text class="segment-label" x="431" y="240">Shortfall</text>
  </g>

  <g class="milestones">
    <text class="milestone-label" x="615" y="58">Revenue $0</text>

    <use href="#milestone-flag" x="1086" y="228" width="48" height="62"/>
    <text class="milestone-label" x="1043" y="247">Gross</text>
    <text class="milestone-label" x="1043" y="275">Margin</text>
    <text class="milestone-label" x="1043" y="303">$0</text>

    <use href="#milestone-flag" x="1078" y="650" width="48" height="62"/>
    <text class="milestone-label" x="1040" y="690">EBIT</text>
    <text class="milestone-label" x="1040" y="718">$0</text>

    <use href="#milestone-flag" x="537" y="893" width="48" height="62"/>
    <text class="milestone-label" x="648" y="922">Retained</text>
    <text class="milestone-label" x="648" y="950">Income $0</text>

    <use class="flag--soft" href="#milestone-flag" x="68" y="655" width="48" height="62"/>
    <text class="milestone-label" x="167" y="650">After</text>
    <text class="milestone-label" x="167" y="678">Working</text>
    <text class="milestone-label" x="167" y="706">Capital</text>
    <text class="milestone-label" x="167" y="734">$0</text>

    <use class="flag--soft" href="#milestone-flag" x="68" y="232" width="48" height="62"/>
    <text class="milestone-label" x="172" y="228">After</text>
    <text class="milestone-label" x="172" y="256">Additional</text>
    <text class="milestone-label" x="172" y="284">Funding</text>
    <text class="milestone-label" x="172" y="312">$0</text>
  </g>
</svg>
</body>
</html>
```